High Tech Real Estate Startup needs a business card

We are developing an innovative real estate marketing product based around advanced search and virtual reality.

We talk to people, we need business cards.

Target Market(s)

The target market is technology professionals and realtors.

Contact Information for Business Card

The information to be included will include

Name
Title
Phone Number
E-mail Address
www.zelquin.com

It should use simple iconography for each one of those fields.

Font styles to use
Other font styles liked:
• Co, Jubilat, Avenir

Colors

Designer to choose colors to be used in the design.

Requirements
Must have
• Clean aesthetic,
• Good use of negative space.
• It should use our company logo, shown in the attached file. It is able to use the negative of that logo (coloured font and white background) and I have attached other acceptable accent colours in a swatch file.
Should not have
• Should not be too busy
• No extraneous text (slogans, tag lines etc)

```html
<!DOCTYPE html>
<html lang="en">
<head>
<meta charset="utf-8">
<title>Zelquin Business Card</title>
<link rel="stylesheet" href="https://fonts.googleapis.com/css2?family=Roboto:wght@400;500&family=Roboto+Condensed:wght@400;500&display=swap">
<style>
  :root {
    --teal: #03babd;
    --white: #ffffff;
    --ink: #4a4a4a;
    --backdrop: #262626;
    --web-tint: #d9f6f6;
  }
  * { margin: 0; padding: 0; box-sizing: border-box; }
  html, body { width: 1200px; height: 960px; overflow: hidden; }
  body {
    background: var(--backdrop);
    position: relative;
    font-family: "Roboto", Arial, sans-serif;
  }
  .card {
    position: absolute;
    width: 600px;
    height: 342px;
    overflow: hidden;
  }
  .card-front {
    left: 322px; top: 108px;
    background: var(--teal);
    color: var(--white);
    text-align: center;
  }
  .card-front .wordmark {
    position: absolute;
    left: 0; right: 0; top: 126px;
    font-size: 76px;
    font-weight: 500;
    letter-spacing: 3px;
    line-height: 1;
  }
  .card-front .web {
    position: absolute;
    left: 0; right: 0; top: 260px;
    font-size: 14px;
    letter-spacing: 4.5px;
    color: var(--web-tint);
  }
  .card-back {
    left: 320px; top: 493px;
    background: var(--white);
  }
  .card-back .curve { position: absolute; inset: 0; }
  .person {
    position: absolute;
    right: 32px; top: 26px;
    text-align: right;
  }
  .person .name {
    font-family: "Roboto Condensed", Arial, sans-serif;
    font-weight: 500;
    font-size: 25px;
    color: var(--teal);
    line-height: 1;
  }
  .person .title {
    font-family: "Roboto Condensed", Arial, sans-serif;
    font-weight: 500;
    font-size: 15px;
    color: var(--ink);
    margin-top: 5px;
  }
  .card-back .wordmark {
    position: absolute;
    left: 33px; top: 163px;
    font-size: 62px;
    font-weight: 500;
    letter-spacing: 2px;
    color: var(--white);
    line-height: 1;
  }
  .contact {
    position: absolute;
    left: 34px; top: 254px;
    list-style: none;
    color: var(--white);
    font-size: 14px;
  }
  .contact li {
    display: flex;
    align-items: center;
    height: 19.5px;
  }
  .contact svg { width: 14px; height: 14px; margin-right: 8px; fill: var(--white); }
</style>
</head>
<body>
  <section class="card card-front">
    <div class="wordmark">ZELQUIN</div>
    <div class="web">WWW.ZELQUIN.COM</div>
  </section>

  <section class="card card-back">
    <svg class="curve" viewBox="0 0 600 342" preserveAspectRatio="none" aria-hidden="true">
      <path d="M0 40 Q 420 0 600 312 L600 342 L0 342 Z" fill="var(--teal)"/>
      <path d="M0 30 Q 400 2 560 210 Q 390 10 0 34 Z" fill="var(--teal)"/>
    </svg>
    <div class="person">
      <div class="name">DANA HOLLIS</div>
      <div class="title">CEO/FOUNDER</div>
    </div>
    <div class="wordmark">ZELQUIN</div>
    <ul class="contact">
      <li>
        <svg viewBox="0 0 24 24"><path d="M6.6 10.8a15.1 15.1 0 0 0 6.6 6.6l2.2-2.2a1 1 0 0 1 1-.25 11.4 11.4 0 0 0 3.6.57 1 1 0 0 1 1 1V20a1 1 0 0 1-1 1A17 17 0 0 1 3 4a1 1 0 0 1 1-1h3.5a1 1 0 0 1 1 1c0 1.25.2 2.45.57 3.57a1 1 0 0 1-.25 1z"/></svg>
        555 014 2290
      </li>
      <li>
        <svg viewBox="0 0 24 24"><path d="M2 5h20v2l-10 6L2 7z M2 9l10 6 10-6v10H2z"/></svg>
        dana@zelquin.com
      </li>
      <li>
        <svg viewBox="0 0 24 24"><circle cx="12" cy="12" r="10"/><path d="M7 6c2 1 3 3 2 5s-3 2-3 4M14 4c-1 2 1 4 3 4s2 3 1 5-3 2-3 5" stroke="var(--teal)" stroke-width="2" fill="none"/></svg>
        www.zelquin.com
      </li>
    </ul>
  </section>
</body>
</html>
```